Launching a new real estate agency in Monaco

Hello, I am opening a new real estate agency in Monaco. For the purpose of my activity, in order to be known quickly among a fierce competition I need an advertising campaign that will be broadcast in local magazines, newspapers, paper board, etc.

You will find example of pictures of Monaco on which I have the rights and my logo. You can always pick other images that I can buy if the price is reasonable for a commercial use (<200 $)

Please respect the color code.

I wish you good luck and look forward to give you my feedbacks

Reason: Only few projects posted were respecting the brief and of quality. Hoping to receive more in coming days

Target Market(s)

International high-end clientele of all ages, all genders.

Industry/Entity Type

Real Estate Agent

Font styles to use
Serif

Requirements
Must have
• 1/ My logo
• 2/ This message "Un nouveau regard sur l'immobilier" means in English a fresh look at real estate or new eyes on real-estate.
• 3/ My address: 14 rue des Ormeaux, Galerie Bellerive Nord, 98 000 Monaco
• 4/ Phone number: +377.93.48.25.07
• 5/ Website: www.corvano-immo.com.
• 6/ Format: Files should be easily adjustable but I'd like a vertical display to fit easily in Magazines, Poster and billboard. So please work in high resolution !
Nice to have
• Please think about your design in accordance with the message I want to display.
Should not have
• A simple poster with a picture of Monaco that does not take into consideration the message of the advertisement, "Un nouveau regard sur l'immobilier" which means in english, new eyes on real-estate or a new look at real-estate, or new vision at real-estate.

```html
<!DOCTYPE html>
<html lang="fr">
<head>
<meta charset="utf-8">
<title>Corvano Agency — Un nouveau regard sur l'immobilier</title>
<link rel="stylesheet" href="https://fonts.googleapis.com/css2?family=Cinzel:wght@400&family=Arimo:wght@400&display=swap">
<style>
  :root {
    --taupe: #806f58;
    --espresso: #432f2f;
    --paper: #f6f6f4;
    --paper-edge: #e4e4e2;
    --copper: #c98f6a;
    --copper-line: #b87a5c;
    --ink-light: #ffffff;
    --pin-red: #d8121b;
  }
  * { margin: 0; padding: 0; box-sizing: border-box; }
  html, body { width: 849px; height: 1200px; overflow: hidden; background: var(--espresso); }
  .poster {
    position: relative;
    width: 849px;
    height: 1200px;
    background: linear-gradient(to bottom, var(--taupe) 0, var(--taupe) 596px, var(--espresso) 596px, var(--espresso) 100%);
    overflow: hidden;
  }
  .polaroid {
    position: absolute;
    left: 138px;
    top: 238px;
    width: 572px;
    height: 574px;
    background: linear-gradient(135deg, #ffffff 0%, var(--paper) 55%, var(--paper-edge) 100%);
    box-shadow: 0 14px 22px rgba(0,0,0,0.45), 0 2px 4px rgba(0,0,0,0.25);
  }
  .polaroid-photo {
    position: absolute;
    left: 44px;
    top: 48px;
    width: 482px;
    height: 396px;
    background:
      linear-gradient(to bottom,
        #f2a63a 0%, #e2865a 5%, #b77a9a 14%, #a986ad 30%, #9c7aa3 48%,
        #6d4f62 62%, #5a3a36 74%, #8a5a2e 86%, #3d2a22 100%);
    box-shadow: inset 0 0 3px rgba(0,0,0,0.5), 0 1px 2px rgba(0,0,0,0.3);
  }
  .tagline {
    position: absolute;
    left: 0;
    right: 0;
    top: 470px;
    text-align: center;
    font-family: "Cinzel", serif;
    font-weight: 400;
    font-size: 35px;
    line-height: 36px;
    letter-spacing: 0.5px;
    color: var(--copper);
  }
  .pin {
    position: absolute;
    left: 362px;
    top: 190px;
    width: 60px;
    height: 72px;
  }
  .brand {
    position: absolute;
    left: 84px;
    top: 1040px;
    display: flex;
    align-items: center;
    gap: 14px;
    font-family: "Cinzel", serif;
    font-weight: 400;
    font-size: 34px;
    letter-spacing: 2px;
    color: var(--copper);
  }
  .brand-mark {
    width: 18px;
    height: 18px;
    background: var(--copper);
  }
  .contact {
    position: absolute;
    right: 84px;
    top: 1016px;
    width: 320px;
    text-align: right;
    font-family: "Arimo", Arial, sans-serif;
    color: var(--ink-light);
  }
  .contact-address { font-size: 14px; line-height: 20px; }
  .contact-phone {
    font-size: 30px;
    line-height: 34px;
    margin-top: 2px;
    padding-bottom: 4px;
    border-bottom: 1px solid var(--copper-line);
  }
  .contact-web { font-size: 14px; line-height: 18px; margin-top: 6px; }
</style>
</head>
<body>
  <main class="poster">
    <section class="polaroid">
      <div class="polaroid-photo" role="img" aria-label="Aerial view of Monaco's coastline at sunset, city lights along the bay"></div>
      <h1 class="tagline">Un nouveau regard<br>sur l'immobilier"</h1>
    </section>

    <svg class="pin" viewBox="0 0 60 72" aria-hidden="true">
      <line x1="30" y1="34" x2="46" y2="62" stroke="#9a9a9a" stroke-width="2.5" stroke-linecap="round"/>
      <ellipse cx="38" cy="40" rx="12" ry="8" fill="var(--pin-red)" transform="rotate(-35 38 40)"/>
      <circle cx="24" cy="22" r="17" fill="var(--pin-red)"/>
      <circle cx="19" cy="16" r="5" fill="#ff6a6a" opacity="0.6"/>
    </svg>

    <div class="brand">
      <span class="brand-mark"></span>
      <span class="brand-name">Corvano Agency</span>
    </div>

    <address class="contact" style="font-style: normal;">
      <p class="contact-address">14 rue des Ormeaux,<br>Galerie Bellerive Nord, 98 000 Monaco</p>
      <p class="contact-phone">Ph.: +377.93.48.25.07</p>
      <p class="contact-web">www.corvano-immo.com</p>
    </address>
  </main>
</body>
</html>
```